Landing Page Design for Adult Dating Age Verification (18+)

The objective of this task is to design a visually appealing pre-landing page for the adult dating site "Quillmera (site: https://quillmera.com/)" with an age verification mechanism. The pre-landing page will feature two buttons that redirect visitors to the main offer. The design should also include a footer block that includes links to the terms of use, privacy policy, and contact us pages.

Design Requirements:
Develop an age verification section prominently displayed on the pre-landing page.
Design the section to include two buttons labeled "Yes" and "No" for visitors to confirm their age.
Ensure the section is visually appealing and clearly communicates the purpose of age verification.

Visual Appeal:
Create a visually appealing design that aligns with the branding and theme of the "Quillmera" adult dating site.
Use suitable color schemes, typography, and graphics to enhance the overall visual appeal of the pre-landing page.

Layout and Navigation:
Design an engaging and intuitive layout that encourages visitors to interact with the page and proceed to the main offer.
Ensure clear and visible navigation elements that direct visitors to the main offer or provide additional information.

Responsive Design:
Develop a responsive design that provides a seamless user experience across various devices, including desktop and mobile.
Ensure the design elements and layout adapt well to different screen sizes and resolutions.

File Formats and Assets:
Deliver the final design in PSD, AI, or Sketch format, ensuring that the files are well-organized and layered.
Include any necessary images or assets used in the design, ensuring they are of high quality and optimized for web use.

```html
<!DOCTYPE html>
<html lang="en">
<head>
<meta charset="utf-8">
<title>Quillmera — Age Verification</title>
<link href="https://fonts.googleapis.com/css2?family=Roboto:wght@400;500;700&display=swap" rel="stylesheet">
<style>
  :root {
    --lilac: #d4b5d8;
    --lilac-border: #d3b2dc;
    --ink: #222228;
    --brand-ink: #23232f;
    --badge: #fa5257;
    --white: #ffffff;
    --panel: rgba(238, 234, 240, 0.82);
    --footer-text: #2c2c30;
  }
  * { box-sizing: border-box; margin: 0; padding: 0; }
  html, body { width: 1200px; height: 857px; overflow: hidden; }
  body { font-family: "Roboto", Arial, sans-serif; position: relative; background: var(--white); }

  .hero {
    position: absolute; left: 0; top: 0; width: 1200px; height: 742px;
    background:
      radial-gradient(ellipse at 85% 10%, #fbf7f2 0%, rgba(251,247,242,0) 45%),
      radial-gradient(ellipse at 60% 45%, #e9c3ac 0%, rgba(233,195,172,0) 50%),
      linear-gradient(180deg, #d8cfc6 0%, #cdb5a6 45%, #a99a9e 75%, #8a8089 100%);
  }

  .brand {
    position: absolute; left: 0; top: 36px; width: 1200px;
    display: flex; justify-content: center; align-items: center; gap: 16px;
  }
  .brand-dot { width: 80px; height: 80px; border-radius: 50%; background: var(--lilac); }
  .brand-name { font-size: 48px; font-weight: 700; color: var(--brand-ink); letter-spacing: 1px; }

  .verify {
    position: absolute; left: 219px; top: 219px; width: 762px; height: 416px;
    background: var(--panel); border: 2px solid var(--lilac-border);
    text-align: center;
  }
  .verify-badge {
    position: absolute; left: 318px; top: 62px; width: 126px; height: 126px;
    border-radius: 50%; background: var(--badge); color: var(--white);
    display: flex; align-items: center; justify-content: center;
    font-size: 52px; font-weight: 400; letter-spacing: -2px;
  }
  .verify-title {
    position: absolute; left: 0; top: 200px; width: 100%;
    font-size: 62px; font-weight: 700; color: var(--ink); line-height: 74px;
  }
  .verify-actions {
    position: absolute; left: 0; top: 300px; width: 100%;
    display: flex; justify-content: center; gap: 18px;
  }
  .btn {
    width: 122px; height: 51px; border-radius: 26px;
    font: 700 21px "Roboto", Arial, sans-serif; color: var(--ink);
    display: flex; align-items: center; justify-content: center;
    text-decoration: none;
  }
  .btn-yes { background: var(--lilac); }
  .btn-no { border: 2px solid var(--lilac-border); background: transparent; }

  .site-footer {
    position: absolute; left: 0; top: 742px; width: 1200px; height: 115px;
    background: var(--lilac); color: var(--footer-text);
  }
  .footer-links { position: absolute; left: 125px; top: 48px; display: flex; gap: 43px; }
  .footer-links a { color: var(--footer-text); text-decoration: none; font-size: 17px; }
  .footer-copy { position: absolute; left: 674px; top: 50px; font-size: 15.5px; }
</style>
</head>
<body>
  <div class="hero" role="img" aria-label="Photo of a couple embracing on a bed in a bright, warm bedroom"></div>

  <header class="brand">
    <span class="brand-dot"></span>
    <span class="brand-name">Quillmera</span>
  </header>

  <section class="verify">
    <div class="verify-badge">18+</div>
    <h1 class="verify-title">Age Verification</h1>
    <div class="verify-actions">
      <a class="btn btn-yes" href="https://quillmera.com/">Yes</a>
      <a class="btn btn-no" href="#">No</a>
    </div>
  </section>

  <footer class="site-footer">
    <nav class="footer-links">
      <a href="#">Terms of use</a>
      <a href="#">Privacy policy</a>
      <a href="#">Contact us</a>
    </nav>
    <p class="footer-copy">©Copyrights 2023 Company Name &nbsp;| &nbsp;&nbsp;All Rights Reserved</p>
  </footer>
</body>
</html>
```